Onboarding Carousel UI/UX design

We need a great UI/UX design for our onboarding carousel as attached in the PDF document. The chosen designers will be given our brand book with colors and styles to be used. The images must be focused on the content of each slide and be professional unique style (Do not use the childish cartoons we have used for placeholders)

Industry/Entity Type

Mortgage Brokerage

Number of Pages Required

5+ page

Font styles to use
Other font styles liked:
• Roboto

Requirements
Must have
• Great UI / UX design
Very relevant content of the images to match the slide
Nice to have
• Brand book

https://pv.lumorak.com/view/ed991dda-3474-4c3e-9747-882e21ba3df5-b8ca/?fullscreen

Image styles we like. Would need to be customized and made unique for us.

https://pinvarlo.com/shots/6300615-Torvane-Quillet-Illustration-Collaboration
https://meltridgestudio.co.za/software-client-style-frames
Should not have
• Do not use the childish images we have used as placeholders

```html
<!DOCTYPE html>
<html lang="en">
<head>
<meta charset="utf-8">
<title>Onboarding Carousel</title>
<link href="https://fonts.googleapis.com/css2?family=Roboto:wght@400;500;700&display=swap" rel="stylesheet">
<style>
  :root {
    --canvas: #e3e5e8;
    --screen: #ffffff;
    --ink: #132c45;
    --body: #6e7480;
    --brand: #0563c1;
    --brand-soft: #5aa6e6;
    --art-a: #d9ecf6;
    --art-b: #c4e9ef;
  }
  * { box-sizing: border-box; margin: 0; padding: 0; }
  html, body {
    width: 1200px; height: 806px; overflow: hidden;
    background: var(--canvas);
    font-family: "Roboto", sans-serif;
  }
  .carousel { position: relative; width: 1200px; height: 806px; }
  .screen {
    position: absolute; top: 68px;
    width: 309px; height: 669px;
    background: var(--screen);
    border-radius: 40px;
    overflow: hidden;
  }
  .screen--welcome { left: 82px; }
  .screen--account { left: 446px; }
  .screen--secure  { left: 810px; }

  .screen__art {
    position: absolute; left: 28px; top: 34px;
    width: 253px; height: 304px;
    border-radius: 14px;
    background: linear-gradient(160deg, var(--art-a), var(--art-b));
  }
  .screen__title {
    position: absolute; left: 0; right: 0; top: 366px;
    text-align: center; color: var(--ink);
    font-size: 23px; line-height: 31px; font-weight: 400;
  }
  .screen__title strong { font-weight: 700; }
  .screen__text {
    position: absolute; left: 0; right: 0; top: 440px;
    text-align: center; color: var(--body);
    font-size: 13.2px; line-height: 21.5px;
  }
  .pager {
    position: absolute; left: 0; right: 0; top: 510px;
    display: flex; justify-content: center; align-items: center; gap: 6px;
  }
  .pager__dot { width: 6px; height: 6px; border-radius: 50%; background: var(--brand-soft); }
  .pager__dot--active {
    width: 11px; height: 11px;
    border: 1.5px solid var(--brand);
    background: radial-gradient(circle, var(--brand) 0 2.6px, #fff 3px);
  }
  .screen__hint {
    position: absolute; left: 0; right: 0; top: 532px;
    text-align: center; color: var(--brand);
    font-size: 9.6px; font-weight: 500;
  }
  .screen__next {
    position: absolute; left: 99px; top: 588px;
    width: 111px; height: 43px;
    background: var(--brand); color: #fff;
    border: none; border-radius: 3px;
    font: 700 14px "Roboto", sans-serif;
  }
  .screen__signin {
    position: absolute; left: 0; right: 0; top: 641px;
    text-align: center; color: #2a2f36;
    font-size: 11.6px;
  }
  .screen__signin a { color: var(--brand); text-decoration: none; margin-left: 3px; }
</style>
</head>
<body>
<main class="carousel">

  <section class="screen screen--welcome">
    <div class="screen__art" role="img" aria-label="Illustration of a person holding a phone beside an application checklist"></div>
    <h1 class="screen__title"><strong>Welcome to Finance</strong><br>Brokers Apply Online</h1>
    <p class="screen__text">You can apply online for your next<br>mortgage credit in about 20 minutes.</p>
    <div class="pager"><span class="pager__dot pager__dot--active"></span><span class="pager__dot"></span><span class="pager__dot"></span><span class="pager__dot"></span><span class="pager__dot"></span></div>
    <p class="screen__hint">It's easy, and we will guide you all the way.</p>
    <button class="screen__next">Next</button>
    <p class="screen__signin">Have an Account?<a href="#">Sign In</a></p>
  </section>

  <section class="screen screen--account">
    <div class="screen__art" role="img" aria-label="Illustration of a person with a laptop creating a profile"></div>
    <h2 class="screen__title"><strong>#1 Create Your</strong><br>Personal Account</h2>
    <p class="screen__text">You will need a valid email address<br>to create your account</p>
    <div class="pager"><span class="pager__dot pager__dot--active"></span><span class="pager__dot"></span><span class="pager__dot"></span><span class="pager__dot"></span><span class="pager__dot"></span></div>
    <p class="screen__hint">We will send you a confirmation email</p>
    <button class="screen__next">Next</button>
    <p class="screen__signin">Have an Account?<a href="#">Sign In</a></p>
  </section>

  <section class="screen screen--secure">
    <div class="screen__art" role="img" aria-label="Illustration of a person with a phone beside a security shield"></div>
    <h2 class="screen__title"><strong>#2 Secure Your Account</strong><br>With Your Mobile Phone</h2>
    <p class="screen__text">You will need a valid mobile phone number<br>to enable two factor authentication.</p>
    <div class="pager"><span class="pager__dot pager__dot--active"></span><span class="pager__dot"></span><span class="pager__dot"></span><span class="pager__dot"></span><span class="pager__dot"></span></div>
    <p class="screen__hint">We will send you a confirmation email</p>
    <button class="screen__next">Next</button>
    <p class="screen__signin">Have an Account?<a href="#">Sign In</a></p>
  </section>

</main>
</body>
</html>
```